Bicycle Tour Schedule on a Business Card

Need to develop a 2 side business card that highlights a series of bike tours on 1 side and a series of events on the other side.
This will be inserted into a card wallet that attaches to a cell phone and will be handed out at an expo. The card wallets are black and red so color must coordinate with both. There is a photo of the card wallets attached.

1 side needs to be devoted to Pedal Vista Trek and the others to KQR Venture events on the other. Dates and websites are very important.

Target Market(s)

Cyclists
Predominantly men ages 40+
Educated, Professionals

Industry/Entity Type

Business

Font styles to use
Serif

Requirements
Must have
• Pedal vista treks logo on 1 side and KQR Venture logo on the other side
• dates and websites clearly visible
• Design of both sides must go together.
• Must be portrait not landscape

```html
<!DOCTYPE html>
<html lang="en">
<head>
<meta charset="utf-8">
<title>Pedal Vista Treks &amp; KQR Venture – Event Cards</title>
<link rel="stylesheet" href="https://fonts.googleapis.com/css2?family=Open+Sans:ital,wght@0,400;0,600;0,700;1,700&display=swap">
<style>
  :root {
    --backdrop: #9a9b9b;
    --paper: #eeeff0;
    --tour-green: #3aa55b;
    --tour-blue: #0d58a8;
    --camp-blue: #1a8cc2;
    --camp-red: #c41a31;
    --ink-white: #ffffff;
  }
  html, body {
    margin: 0;
    padding: 0;
    width: 1105px;
    height: 1200px;
    overflow: hidden;
    background: var(--backdrop);
    font-family: "Open Sans", Arial, sans-serif;
  }
  .card {
    position: absolute;
    top: 269px;
    width: 398px;
    height: 697px;
    display: flex;
    flex-direction: column;
    background: var(--paper);
  }
  .card--tours { left: 113px; }
  .card--camps { left: 597px; }

  .brand {
    display: flex;
    align-items: center;
    justify-content: center;
    gap: 12px;
    flex: none;
  }
  .card--tours .brand { height: 239px; }
  .card--camps .brand { height: 242px; }
  .brand-name {
    font-weight: 700;
    font-size: 31px;
    letter-spacing: 0.5px;
  }
  .card--tours .brand-name { color: var(--tour-blue); }
  .card--camps .brand-name { color: var(--camp-red); }
  .brand-dot {
    width: 26px; height: 26px; border-radius: 50%;
    background: var(--tour-green);
  }
  .brand-square {
    width: 26px; height: 26px;
    background: var(--camp-red);
  }

  .tagline {
    flex: none;
    display: flex;
    align-items: center;
    justify-content: center;
    text-align: center;
    color: var(--ink-white);
    font-weight: 700;
    font-style: italic;
    line-height: 1.25;
    border-bottom: 4px solid var(--paper);
  }
  .card--tours .tagline {
    height: 101px;
    background: var(--tour-green);
    font-size: 19px;
  }
  .card--camps .tagline {
    height: 59px;
    background: var(--camp-blue);
    font-size: 19px;
  }

  .schedule {
    flex: 1;
    list-style: none;
    margin: 0;
    display: flex;
    flex-direction: column;
    align-items: center;
    color: var(--ink-white);
    text-align: center;
    font-size: 18px;
    line-height: 1.3;
  }
  .card--tours .schedule {
    background: var(--tour-blue);
    padding: 32px 10px 0;
    gap: 16px;
  }
  .card--camps .schedule {
    background: var(--camp-red);
    padding: 22px 10px 0;
    gap: 11px;
  }
  .event-name { display: block; font-weight: 400; }
  .event-date, .event-site { display: block; font-weight: 700; }
</style>
</head>
<body>

<section class="card card--tours">
  <header class="brand">
    <span class="brand-dot"></span>
    <span class="brand-name">Pedal Vista Treks</span>
  </header>
  <div class="tagline">Fully supported bike tours.<br>Discover the hidden gems on<br>two wheels</div>
  <ul class="schedule">
    <li><span class="event-name">Heart of Colorado</span><span class="event-date">June 26 - July 2, 2016</span></li>
    <li><span class="event-name">Colorado Front Range Tour</span><span class="event-date">August 14-20, 2016</span></li>
    <li><span class="event-name">Cape Cod Tour</span><span class="event-date">October 9 -15, 2016</span></li>
    <li><span class="event-name">Florida Key Tours</span><span class="event-date">November 6-12, 2016 &amp;</span><span class="event-date">December 4-10, 2016</span></li>
  </ul>
</section>

<section class="card card--camps">
  <header class="brand">
    <span class="brand-square"></span>
    <span class="brand-name">KQR Venture</span>
  </header>
  <div class="tagline">Trail Spin Series:<br>Cycling camps for youth</div>
  <ul class="schedule">
    <li><span class="event-name">Mountain Bike Camp</span><span class="event-date">July 8-10, 2016</span></li>
    <li><span class="event-name">Cyclocross Camp</span><span class="event-date">August 26-28, 2016</span><span class="event-site">Trailspinseries.org</span></li>
    <li><span class="event-name">Mile High Hundred Ride</span><span class="event-date">June 18, 2016</span><span class="event-site">Milehighhundred.com</span></li>
    <li><span class="event-name">Rockies Loop 2 Loop Challenge</span><span class="event-date">July 30, 2016 - Rkloop2loop.com</span></li>
    <li><span class="event-name">Zany Pedal Ride</span><span class="event-date">September 11, 2016</span><span class="event-site">zanypedalride.com</span></li>
  </ul>
</section>

</body>
</html>
```